Plenko - Shoe Fitting App : Foot scanning app, 3D reconstruction and Fit recommandation.

We are a startup that has developed a 3D scanning App that compares the 3d reconstructed foot to the 3D Last (mould) of a shoe to find the best match and recommend a shoe size with a graphical representation of the fit on a reconstructed foot without texturing. The challenge of this app is to have a simple and intuitive onboarding of the user with clean and crisp ui and a simple tutorial for foot scanning. 3D representation of the fit is also key. What you see is what you feel is what we would like to achieve.

Target Market(s)

Sneaker Brands and athletic shoes brands

Industry/Entity Type

Footwear

Font styles to use
Other font styles liked:
• Oswald or Droid Serif

Colors
0094D4
00A9DD
6FCCEA
C7EBF8
E9F6FB

Requirements
Must have
• Simple intuitive UI to onboard the customer to scan his bare foot (please look at attached image on how to scan the foot). You must flip your phone so that the screen is facing your foot. Start at 40cm distance form the front of your foot and turn 360% slowly to capture the foot while you feel the aptic of the Phone. That needs to be presented with a simple animation that the user can easily understand and skip if he is a returning customer and knows how to do that. the rest of the UI is to present the result of the scanned foot for the user to use to get his fit and size. The other must have is the final result screen. Where the user will a representation of the foot (snug, loose ) of different predefined areas of the foot so he can choose the fit that he likes and not necessarily the size that we suggest. Must match website design (https://www.plenko.example)
Nice to have
• An animation of the whole process (scan-compare 3d foot with 3d shoe last(or mould) and get the 3D result of the best fit + associated size. Optionaly, an option to play with your foot and transform it (avatar like with accessories and colours)
Should not have
• Too many colours. Too much text. No gender type. No race type.

```html
<!DOCTYPE html>
<html lang="en">
<head>
<meta charset="utf-8">
<title>Plenko Onboarding</title>
<link href="https://fonts.googleapis.com/css2?family=Poppins:wght@700&family=Oswald:wght@500;600&family=Raleway:wght@400;500;700&display=swap" rel="stylesheet">
<style>
  :root{
    --bg:#1c1c1c;
    --band:#000000;
    --ink:#111111;
    --white:#ffffff;
    --peach:#f9cab8;
    --teal:#3fb1b1;
    --violet:#6a5aa8;
    --muted:#8a8a8a;
    --dash:#222222;
    --home:#0f3b33;
  }
  *{margin:0;padding:0;box-sizing:border-box}
  html,body{width:1200px;height:491px;overflow:hidden;background:var(--bg)}
  .board{position:relative;width:1200px;height:491px;background:var(--bg);color:var(--white)}
  .board-title{position:absolute;left:200px;top:22px;font:700 70px/1 'Poppins',sans-serif;letter-spacing:-1px}
  .spec-heading{position:absolute;top:34px;font:700 24px/1 'Poppins',sans-serif;letter-spacing:-.5px}
  .spec-fonts{left:668px}
  .spec-colors{left:862px}
  .font-display{position:absolute;left:668px;top:74px;font:600 27px/1 'Oswald',sans-serif;white-space:pre}
  .font-body{position:absolute;left:668px;top:114px;font:400 15px/1 'Raleway',sans-serif;white-space:pre}
  .font-body b{font-weight:500}
  .swatch{position:absolute;top:77px;width:37px;height:37px;border-radius:4px}
  .swatch-gradient{left:862px;background:linear-gradient(135deg,var(--teal),var(--violet))}
  .swatch-dark{left:905px;background:var(--ink)}
  .swatch-peach{left:948px;background:var(--peach)}
  .swatch-white{left:992px;background:var(--white)}

  .strip{position:absolute;left:65px;top:164px;width:1071px;height:231px;background:var(--band)}
  .splash{position:absolute;left:65px;top:164px;width:107px;height:231px;background:var(--ink);border-radius:5px;display:flex;align-items:center;justify-content:center}
  .splash-name{font:700 19px/1 'Raleway',sans-serif;color:var(--white);letter-spacing:.5px;margin-top:16px}

  .screen{position:absolute;top:164px;width:107px;height:231px;background:var(--white);border-radius:6px;color:var(--ink)}
  .status{position:absolute;left:8px;right:6px;top:5px;display:flex;justify-content:space-between;align-items:center;font:600 5px/1 'Raleway',sans-serif}
  .status svg{display:block}
  .skip{position:absolute;right:12px;top:22px;font:500 5.5px/1 'Oswald',sans-serif}
  .art{position:absolute;left:10px;top:44px;width:87px;height:90px;border-radius:42% 58% 50% 46%/48% 40% 60% 52%;background:linear-gradient(135deg,var(--teal) 10%,var(--violet) 90%);opacity:.9}
  .step-title{position:absolute;left:4px;right:4px;top:143px;text-align:center;font:500 10px/12px 'Oswald',sans-serif}
  .step-text{position:absolute;left:8px;right:8px;top:174px;text-align:center;font:400 4.2px/6.5px 'Raleway',sans-serif;color:var(--muted)}
  .dots{position:absolute;left:0;right:0;top:192px;display:flex;justify-content:center;gap:1.2px}
  .dots i{display:block;width:3.2px;height:1px;background:var(--dash)}
  .dots i.on{width:5.5px;background:linear-gradient(90deg,var(--teal),var(--violet))}
  .next{position:absolute;left:7px;right:7px;top:202px;height:13px;background:var(--ink);border-radius:1.5px;color:var(--white);font:500 4.6px/13px 'Raleway',sans-serif;text-align:center}
  .home{position:absolute;left:35px;width:37px;top:223px;height:1.4px;border-radius:1px;background:var(--home)}
</style>
</head>
<body>
<main class="board">
  <h1 class="board-title">Onboarding</h1>

  <h2 class="spec-heading spec-fonts">Font Use:</h2>
  <p class="font-display">H1 , H4  :  Oswald</p>
  <p class="font-body">body, <b>button</b>  :  Raleway</p>

  <h2 class="spec-heading spec-colors">Color:</h2>
  <div class="swatch swatch-gradient"></div>
  <div class="swatch swatch-dark"></div>
  <div class="swatch swatch-peach"></div>
  <div class="swatch swatch-white"></div>

  <div class="strip"></div>
  <section class="splash"><span class="splash-name">Plenko</span></section>

  <section class="screen" style="left:185px">
    <div class="status"><span>9:41</span><svg width="20" height="5" viewBox="0 0 20 5"><rect x="0" y="3" width="1" height="2" fill="#111"/><rect x="1.6" y="2" width="1" height="3" fill="#111"/><rect x="3.2" y="1" width="1" height="4" fill="#111"/><path d="M7 2.2a3 3 0 0 1 4 0M8 3.3a1.5 1.5 0 0 1 2 0" stroke="#111" stroke-width=".6" fill="none"/><rect x="14" y="1" width="5.5" height="3" rx=".8" fill="#111"/></svg></div>
    <span class="skip">Skip</span>
    <div class="art" role="img" aria-label="Illustration of a room lit by two lamps over a city view, with a hand on a light switch"></div>
    <h3 class="step-title">Step 1: Setting Up the Environment</h3>
    <p class="step-text">Ensure two light sources are used to minimize shadows for accurate scanning.</p>
    <div class="dots"><i class="on"></i><i></i><i></i><i></i><i></i><i></i><i></i></div>
    <div class="next">Next</div><div class="home"></div>
  </section>

  <section class="screen" style="left:305px">
    <div class="status"><span>9:41</span><svg width="20" height="5" viewBox="0 0 20 5"><rect x="0" y="3" width="1" height="2" fill="#111"/><rect x="1.6" y="2" width="1" height="3" fill="#111"/><rect x="3.2" y="1" width="1" height="4" fill="#111"/><path d="M7 2.2a3 3 0 0 1 4 0M8 3.3a1.5 1.5 0 0 1 2 0" stroke="#111" stroke-width=".6" fill="none"/><rect x="14" y="1" width="5.5" height="3" rx=".8" fill="#111"/></svg></div>
    <span class="skip">Skip</span>
    <div class="art" role="img" aria-label="Illustration of a person removing shoes and rolling up trousers"></div>
    <h3 class="step-title">Step 2: Prepare Your Feet</h3>
    <p class="step-text">Remove shoes and roll up pants for full foot visibility.</p>
    <div class="dots"><i></i><i class="on"></i><i></i><i></i><i></i><i></i><i></i></div>
    <div class="next">Next</div><div class="home"></div>
  </section>

  <section class="screen" style="left:426px">
    <div class="status"><span>9:41</span><svg width="20" height="5" viewBox="0 0 20 5"><rect x="0" y="3" width="1" height="2" fill="#111"/><rect x="1.6" y="2" width="1" height="3" fill="#111"/><rect x="3.2" y="1" width="1" height="4" fill="#111"/><path d="M7 2.2a3 3 0 0 1 4 0M8 3.3a1.5 1.5 0 0 1 2 0" stroke="#111" stroke-width=".6" fill="none"/><rect x="14" y="1" width="5.5" height="3" rx=".8" fill="#111"/></svg></div>
    <span class="skip">Skip</span>
    <div class="art" role="img" aria-label="Illustration of a seated person resting an elbow on the knee"></div>
    <h3 class="step-title">Step 3: Stabilizing Your Hand</h3>
    <p class="step-text">Rest your elbow on your knee to maintain a stable hand position.</p>
    <div class="dots"><i></i><i></i><i class="on"></i><i></i><i></i><i></i><i></i></div>
    <div class="next">Next</div><div class="home"></div>
  </section>

  <section class="screen" style="left:546px">
    <div class="status"><span>9:41</span><svg width="20" height="5" viewBox="0 0 20 5"><rect x="0" y="3" width="1" height="2" fill="#111"/><rect x="1.6" y="2" width="1" height="3" fill="#111"/><rect x="3.2" y="1" width="1" height="4" fill="#111"/><path d="M7 2.2a3 3 0 0 1 4 0M8 3.3a1.5 1.5 0 0 1 2 0" stroke="#111" stroke-width=".6" fill="none"/><rect x="14" y="1" width="5.5" height="3" rx=".8" fill="#111"/></svg></div>
    <span class="skip">Skip</span>
    <div class="art" role="img" aria-label="Illustration of a hand holding a phone with the screen facing out"></div>
    <h3 class="step-title">Step 4: Flip Your Phone</h3>
    <p class="step-text">Turn your device to activate the front-facing sensors for precise depth scanning.</p>
    <div class="dots"><i></i><i></i><i></i><i class="on"></i><i></i><i></i><i></i></div>
    <div class="next">Next</div><div class="home"></div>
  </section>

  <section class="screen" style="left:667px">
    <div class="status"><span>9:41</span><svg width="20" height="5" viewBox="0 0 20 5"><rect x="0" y="3" width="1" height="2" fill="#111"/><rect x="1.6" y="2" width="1" height="3" fill="#111"/><rect x="3.2" y="1" width="1" height="4" fill="#111"/><path d="M7 2.2a3 3 0 0 1 4 0M8 3.3a1.5 1.5 0 0 1 2 0" stroke="#111" stroke-width=".6" fill="none"/><rect x="14" y="1" width="5.5" height="3" rx=".8" fill="#111"/></svg></div>
    <span class="skip">Skip</span>
    <div class="art" role="img" aria-label="Illustration of a phone held 40 cm in front of a bare foot"></div>
    <h3 class="step-title">Step 5: Positioning Your Phone</h3>
    <p class="step-text">Hold your phone 40 cm away and keep it steady.</p>
    <div class="dots"><i></i><i></i><i></i><i></i><i class="on"></i><i></i><i></i></div>
    <div class="next">Next</div><div class="home"></div>
  </section>

  <section class="screen" style="left:787px">
    <div class="status"><span>9:41</span><svg width="20" height="5" viewBox="0 0 20 5"><rect x="0" y="3" width="1" height="2" fill="#111"/><rect x="1.6" y="2" width="1" height="3" fill="#111"/><rect x="3.2" y="1" width="1" height="4" fill="#111"/><path d="M7 2.2a3 3 0 0 1 4 0M8 3.3a1.5 1.5 0 0 1 2 0" stroke="#111" stroke-width=".6" fill="none"/><rect x="14" y="1" width="5.5" height="3" rx=".8" fill="#111"/></svg></div>
    <span class="skip">Skip</span>
    <div class="art" role="img" aria-label="Illustration of a phone moving around a bare foot"></div>
    <h3 class="step-title">Step 6: Scanning Your Foot</h3>
    <p class="step-text">Slowly move your upper body around your foot while keeping your elbow steady.</p>
    <div class="dots"><i></i><i></i><i></i><i></i><i></i><i class="on"></i><i></i></div>
    <div class="next">Next</div><div class="home"></div>
  </section>

  <section class="screen" style="left:908px">
    <div class="status"><span>9:41</span><svg width="20" height="5" viewBox="0 0 20 5"><rect x="0" y="3" width="1" height="2" fill="#111"/><rect x="1.6" y="2" width="1" height="3" fill="#111"/><rect x="3.2" y="1" width="1" height="4" fill="#111"/><path d="M7 2.2a3 3 0 0 1 4 0M8 3.3a1.5 1.5 0 0 1 2 0" stroke="#111" stroke-width=".6" fill="none"/><rect x="14" y="1" width="5.5" height="3" rx=".8" fill="#111"/></svg></div>
    <span class="skip">Skip</span>
    <div class="art" role="img" aria-label="Illustration of a bare foot with a curved arrow circling it"></div>
    <h3 class="step-title">Step 7: Completing the Scan</h3>
    <p class="step-text">Maintain a consistent distance and capture all angles.</p>
    <div class="dots"><i></i><i></i><i></i><i></i><i></i><i></i><i class="on"></i><i></i></div>
    <div class="next">Next</div><div class="home"></div>
  </section>

  <section class="screen" style="left:1028px">
    <div class="status"><span>9:41</span><svg width="20" height="5" viewBox="0 0 20 5"><rect x="0" y="3" width="1" height="2" fill="#111"/><rect x="1.6" y="2" width="1" height="3" fill="#111"/><rect x="3.2" y="1" width="1" height="4" fill="#111"/><path d="M7 2.2a3 3 0 0 1 4 0M8 3.3a1.5 1.5 0 0 1 2 0" stroke="#111" stroke-width=".6" fill="none"/><rect x="14" y="1" width="5.5" height="3" rx=".8" fill="#111"/></svg></div>
    <span class="skip">Skip</span>
    <div class="art" role="img" aria-label="Illustration of two bare feet side by side"></div>
    <h3 class="step-title">Step 8: Repeat for the Other Foot</h3>
    <p class="step-text">Follow the same scanning process to ensure accurate data for both feet.</p>
    <div class="dots"><i></i><i></i><i></i><i></i><i></i><i></i><i></i><i class="on"></i></div>
    <div class="next">Next</div><div class="home"></div>
  </section>
</main>
</body>
</html>
```